Income Tax and Accounting Brochure

I need a brochure using my new logo (file attached). I do tax work and accounting work. I am an EA (QFB Enrolled Agent - logo attached) and would like this incorporated into the brochure. I also have a MSA in Accounting. Please incorporate the text that I have provided in the brochure.
Updates

Need extra days to review

Target Market(s)

Tax Clients - both business and individuals

Industry/Entity Type

Accounting

Colors
0054AA
0677BA
7BADD7
CADEEF
E8F1F8

Requirements
Must have
• Use my logo and the QFB EA file in the brochure
Nice to have
• I would like to see a brochure that I can customize with my own text if possible.

```html
<!DOCTYPE html>
<html lang="en">
<head>
<meta charset="utf-8">
<title>Northway Accounting – DL Brochure</title>
<link href="https://fonts.googleapis.com/css2?family=Jost:wght@300;400;500;600&family=Allura&display=swap" rel="stylesheet">
<style>
  :root{
    --navy:#0054AA;
    --blue:#0677BA;
    --sky:#7BADD7;
    --mist:#CADEEF;
    --ice:#E8F1F8;
    --bright:#1a5fd6;
    --red:#c4161c;
    --ink:#333a44;
    --night:#12161d;
    --night-type:#2a303a;
    --panel-pale:#eaf6fc;
  }
  *{box-sizing:border-box;margin:0;padding:0}
  html,body{width:963px;height:1200px;overflow:hidden;background:#fff}
  body{position:relative;font-family:'Jost',sans-serif;color:var(--ink)}

  .sheet-label{position:absolute;left:273px;width:674px;top:70px;text-align:center;
    font-weight:300;font-size:33px;color:#111;letter-spacing:.2px}

  .spread{position:absolute;width:674px;height:477px;display:flex;border:1px solid #9aa3ad}
  .spread--outside{left:273px;top:160px}
  .spread--inside{left:137px;top:658px}
  .panel{position:relative;width:224.7px;height:100%;overflow:hidden}

  /* Cover */
  .cover{position:absolute;left:35px;top:78px;width:225px;height:477px;overflow:hidden}
  .spread .cover{position:relative;left:0;top:0}
  .cover-photo{position:absolute;inset:0;
    background:linear-gradient(180deg,#8ea7c2 0%,#7f9cbc 20%,#9fb5cc 45%,#b9c8d6 62%,#a7c4e0 75%,#c5def5 88%,#b8d7f3 100%)}
  .cover-band{position:absolute;left:0;right:0;top:36px;height:115px;background:rgba(96,146,228,.55)}
  .cover-title{position:absolute;left:0;right:0;top:50px;text-align:center;color:#fff;
    font-weight:300;font-size:27px;line-height:32px;letter-spacing:-.5px}
  .brand{position:absolute;display:flex;align-items:center;gap:6px}
  .cover .brand{left:40px;top:405px}
  .brand-dot{width:34px;height:34px;border-radius:50%;background:var(--navy);flex:none}
  .brand-name{font-weight:600;color:var(--navy);font-size:9.5px;line-height:13px;letter-spacing:.6px;text-transform:uppercase;white-space:nowrap}

  /* About panel */
  .about{background:#fff;text-align:center}
  .about-head{position:absolute;top:39px;left:0;right:0;font-size:13px;font-weight:500;color:var(--bright);line-height:14px}
  .about-role{display:block;font-size:8.5px;color:var(--red);font-weight:400}
  .about-body{position:absolute;top:72px;left:40px;right:40px;font-size:6.6px;line-height:9.5px;font-weight:300}
  .about-body p{margin-bottom:9.5px}
  .about-photo{position:absolute;left:0;right:0;top:263px;height:161px;
    background:linear-gradient(135deg,#6e6a5f,#a39f92 40%,#c9c6bb 60%,#8a857a)}
  .about-tag{position:absolute;top:436px;left:0;right:0;font-size:7px;color:var(--bright);font-weight:300}

  /* Back panel */
  .back{background:var(--night);color:#d9dde3}
  .vert{position:absolute;writing-mode:vertical-rl;transform:rotate(180deg);font-weight:400;color:var(--night-type);white-space:nowrap;line-height:1}
  .vert--small{left:4px;top:15px;height:310px;font-size:35px;text-align:left}
  .vert--large{left:172px;top:-4px;height:482px;font-size:64px;text-align:right}
  .back-contact{position:absolute;top:126px;left:0;right:0;text-align:center;font-size:7px;line-height:19px;font-weight:300}
  .back .brand{left:44px;top:342px}
  .back .brand-name{color:#2f7fe0}
  .badge{position:absolute;left:52px;top:394px;width:124px;height:32px;background:#fff;border-radius:1px}
  .badge-seal{position:absolute;left:3px;top:3px;width:50px;height:26px;border:2px solid #7bbfa6}

  /* Inside panels */
  .prep{background:linear-gradient(180deg,#eef8fd 0%,#cfe6f8 45%,#a9d2f5 75%,#8ec5f3 100%);text-align:center}
  .script{font-family:'Allura',cursive;color:var(--bright);font-weight:400}
  .script-line{position:absolute;white-space:nowrap;line-height:1}
  .prep .l1{left:38px;top:34px;font-size:27px}
  .prep .l2{right:28px;top:62px;font-size:27px}
  .prep-lead{position:absolute;top:107px;left:22px;right:22px;font-size:6.8px;line-height:11.5px;color:var(--red);font-weight:300}
  .prep-body{position:absolute;top:145px;left:20px;right:20px;font-size:6.6px;line-height:11.4px;font-weight:300}
  .prep-body p{margin-bottom:11.3px}
  .word-cloud{position:absolute;left:22px;top:315px;width:182px;height:138px;border-radius:4px;
    background:radial-gradient(ellipse at 50% 55%,#3b57c9 0%,#6a7fd8 35%,rgba(140,110,200,.35) 65%,rgba(140,197,243,0) 85%)}

  .get{background:#fff;text-align:center}
  .get-photo{position:absolute;left:0;right:0;top:34px;height:144px;
    background:linear-gradient(135deg,#1c2c48,#3a5a86 45%,#6f93bd 60%,#243a5c)}
  .get .l1{left:0;right:0;top:208px;font-size:25px;text-align:center}
  .get-list{position:absolute;top:260px;left:28px;right:26px;list-style:none;font-size:6.6px;line-height:11.4px;font-weight:300}
  .get-list li{margin-bottom:11.3px}
  .get-list li::before{content:"• "}

  .books{background:var(--panel-pale);text-align:center}
  .books .l1{left:38px;top:36px;font-size:27px}
  .books .l2{right:26px;top:64px;font-size:27px}
  .books-photo{position:absolute;left:0;right:0;top:132px;height:152px;
    background:linear-gradient(135deg,#e4e6e3,#c8c3b8 40%,#8b7e70 55%,#d9dcda)}
  .books-body{position:absolute;top:320px;left:30px;right:28px;font-size:6.6px;line-height:11.4px;font-weight:300}
  .books-body p{margin-bottom:11.3px}
  .books-body .callout{font-size:10.5px;color:var(--bright);font-weight:300;margin-bottom:12px}
</style>
</head>
<body>

<div class="cover">
  <div class="cover-photo" role="img" aria-label="Photo of hands using a calculator beside a laptop and printed charts"></div>
  <div class="cover-band"></div>
  <h1 class="cover-title">TAX &amp;<br>ACCOUNTING<br>SERVICES</h1>
  <div class="brand"><span class="brand-dot"></span><span class="brand-name">Northway Accounting<br>&amp; Consulting, LLC</span></div>
</div>

<p class="sheet-label">A4 page folded to DL size</p>

<section class="spread spread--outside">
  <div class="panel about">
    <h2 class="about-head">About Marian D Holloway,<span class="about-role">MSA EA (Principal)</span></h2>
    <div class="about-body">
      <p>I have a Masters' Degree in accounting and am an QFB Enrolled Agent.</p>
      <p>I am also a LedgerBooks Advanced Certified Consultant in both the online and desktop products including Enterprise and Point of Sale.</p>
      <p>I provide individual and small business tax services, Accounting, bookkeeping, QFB representation, insurance audit representation, business license assistance and more.</p>
      <p>I have experience working with a wide variety of clients from the point where they first decide they want to start a business.</p>
      <p>They are often unsure about what to do first. I have a lot of experience to offer you.</p>
    </div>
    <div class="about-photo" role="img" aria-label="Photo of a shop owner in a mask holding up an open sign"></div>
    <p class="about-tag">What a joy it is to watch success in action!</p>
  </div>

  <div class="panel back">
    <span class="vert vert--small">REDUCING TAX</span>
    <span class="vert vert--large">ACCOUNTING</span>
    <p class="back-contact">Address and<br>Contact Details</p>
    <div class="brand"><span class="brand-dot"></span><span class="brand-name">Northway Accounting<br>&amp; Consulting, LLC</span></div>
    <div class="badge" aria-label="Enrolled agent credential badge"><span class="badge-seal"></span></div>
  </div>

  <div class="panel cover">
    <div class="cover-photo" role="img" aria-label="Photo of hands using a calculator beside a laptop and printed charts"></div>
    <div class="cover-band"></div>
    <h1 class="cover-title">TAX &amp;<br>ACCOUNTING<br>SERVICES</h1>
    <div class="brand"><span class="brand-dot"></span><span class="brand-name">Northway Accounting<br>&amp; Consulting, LLC</span></div>
  </div>
</section>

<section class="spread spread--inside">
  <div class="panel prep">
    <h2 class="script"><span class="script-line l1">Tax Preparation</span><span class="script-line l2">Why hire us?</span></h2>
    <p class="prep-lead">Preparing your own income tax return can be a task that leaves you with more questions than answers.</p>
    <div class="prep-body">
      <p>According to a study released by the US Government's National Audit Bureau last year, most taxpayers (77% of 71 million taxpayers) believe they benefited from using a professional tax preparer.</p>
      <p>Whether we like it or not, today's tax laws are so complicated that filing a relatively simple return can be confusing.</p>
      <p>It is just too easy to overlook deductions and credits to which you are entitled. Even if you use a computer software program there's no substitute for the assistance of an experienced tax professional.</p>
    </div>
    <div class="word-cloud" role="img" aria-label="Word cloud of tax terms centred on the words Income tax"></div>
  </div>

  <div class="panel get">
    <div class="get-photo" role="img" aria-label="Photo of a laptop with glowing financial chart overlays"></div>
    <h2 class="script"><span class="script-line l1">Here's what you get ...</span></h2>
    <ul class="get-list">
      <li>Your tax return will be checked and rechecked by our computer software identifying potential problems the QFB may look at more closely and reviewing the math to limit QFB contacts.</li>
      <li>Your tax return can be filed electronically so you will get a refund back quicker.</li>
      <li>Our staff will show you how to adjust your payroll withholding to get more money back each week. Why give the QFB an interest free loan for up to 16 months.</li>
      <li>We will show you potential deductions to limit your tax liability for next year. In addition, we will give you a sheet of commonly overlooked deductions to limit the following year's tax liability.</li>
    </ul>
  </div>

  <div class="panel books">
    <h2 class="script"><span class="script-line l1">Books a Mess:</span><span class="script-line l2">No Problem!</span></h2>
    <div class="books-photo" role="img" aria-label="Photo of a stressed man at a laptop in a bright office"></div>
    <div class="books-body">
      <p>If you own a small business and haven't kept up your bookkeeping, don't worry.</p>
      <p class="callout">We can help you.</p>
      <p>We'll prepare your bookkeeping for the year, prepare a full Schedule C, as well as your personal income tax return.<br>Then we'll help you set up an easy system that allows you to keep your books in tip-top shape next year.</p>
    </div>
  </div>
</section>

</body>
</html>
```